Business Card Design - Photographer

I am a landscape photographer and I require a business card design. 

I require two designs:
1)  a double sided business card
 and
b)  a single sided business card 

The single sided design can either be the same as the double sided (with just one side having all the information)....or it can be an entire new design. Its up to you.

My corporate colours are (CMYK):

Blue   69, 32, 0, 0
Grey  72,  64,  47,  31
Green  32,  2,  91,  0
Yellow   0, 19, 92, 0
Orange  0, 39, 75, 0

Colour space in final file should be in CMYK.

The details that need to be included on the card:

- Use the provided Logo
- Name: Wiktor Baranowski
- Email:   sales@vistalumeworks.com.au
- Website:    vistalumeworks.com.au
- Twitter:    twitter.com/vistalumeworks
- Facebook:   facebook.com/vistalumeworks
- Mobile  0417 539 662

Please use the attached template to design the logo to the specified size, including the marked bleed lines. I have also attached my logo in PNG (transparent background) and ai format for you to use.

The final file should be:
- Photoshop version with layers so I can edit the name/text etc. All non vector files should be high resolution at 1039 x 697 pixels at 300 dpi.

I also require a file as:
- Vector based PDF

Anyway questions please contact me.

Thank you

Industry/Entity Type

Landscape

Logo styles of interest
Pictorial/Combination Logo
Abstract Logo
Wordmark Logo
Lettermark Logo
Requirements
Must have
• The details that need to be included on the card:

- Use the provided Logo
- Name: Wiktor Baranowski
- Email: sales@vistalumeworks.com.au
- Website: vistalumeworks.com.au
- Twitter: twitter.com/vistalumeworks
- Facebook: facebook.com/vistalumeworks
- Mobile 0417 539 662

```html
<!DOCTYPE html>
<html lang="en">
<head>
<meta charset="utf-8">
<title>Vistalume Works – Business Card</title>
<link rel="stylesheet" href="https://fonts.googleapis.com/css2?family=Cinzel:wght@400;600;700&display=swap">
<style>
  :root {
    --backdrop: #808184;
    --card: #ffffff;
    --ink: #3b3e50;
    --green: #b8d23d;
    --blue: #3d8fcd;
    --radius: 28px;
  }
  * { box-sizing: border-box; margin: 0; padding: 0; }
  html, body {
    width: 976px; height: 1200px; overflow: hidden;
    background: var(--backdrop);
  }
  body { position: relative; font-family: "Cinzel", serif; color: var(--ink); }

  .card {
    position: absolute;
    width: 818px; height: 468px;
    background: var(--card);
    border-radius: var(--radius);
    overflow: hidden;
  }
  .card--front { left: 83px; top: 105px; }
  .card--back  { left: 89px; top: 642px; width: 817px; }

  .card__rule {
    position: absolute; left: 0; right: 0;
    top: 402px; height: 4px; background: var(--ink);
  }
  .card__band {
    position: absolute; left: 0; right: 0; bottom: 0;
    height: 60px; background: var(--green);
    display: flex; align-items: center; justify-content: center;
  }
  .website { font-size: 15px; font-weight: 700; letter-spacing: 0.5px; color: var(--ink); }
  .website strong { font-size: 21px; font-weight: 700; }

  .brand-mark {
    position: absolute; border-radius: 50%; background: var(--ink);
  }
  .card--front .brand-mark { left: 336px; top: 78px; width: 162px; height: 162px; }
  .card--back .brand-mark  { left: 356px; top: 48px; width: 116px; height: 116px; }

  .brand-name {
    position: absolute; left: 196px; top: 264px; width: 445px;
    text-align: center; font-size: 36px; font-weight: 600;
    letter-spacing: 1px; line-height: 1; white-space: nowrap;
  }
  .brand-line {
    position: absolute; left: 196px; top: 308px; width: 445px; height: 2px;
    background: var(--ink);
  }
  .brand-tagline {
    position: absolute; left: 196px; top: 320px; width: 445px;
    text-align: center; font-size: 16px; font-weight: 700; letter-spacing: 3px;
  }

  .owner-name {
    position: absolute; left: 0; right: 0; top: 184px;
    text-align: center; font-size: 20px; font-weight: 700; letter-spacing: 1px;
  }
  .contact {
    position: absolute; left: 0; right: 0; top: 226px;
    list-style: none; text-align: center;
    font-size: 16px; line-height: 35px; letter-spacing: 0.6px;
  }
  .contact__key { color: var(--blue); font-size: 19px; }
</style>
</head>
<body>
  <section class="card card--front" aria-label="Card front">
    <div class="brand-mark" aria-hidden="true"></div>
    <h1 class="brand-name">VISTALUME WORKS</h1>
    <div class="brand-line"></div>
    <p class="brand-tagline">FINE ART PHOTOGRAPHY</p>
    <div class="card__rule"></div>
    <div class="card__band">
      <p class="website">www.<strong>VISTALUMEWORKS</strong>.com.au</p>
    </div>
  </section>

  <section class="card card--back" aria-label="Card back">
    <div class="brand-mark" aria-hidden="true"></div>
    <p class="owner-name">Wiktor Baranowski</p>
    <ul class="contact">
      <li><span class="contact__key">E</span> : sales@vistalumeworks.com.au</li>
      <li><span class="contact__key">T</span> : twitter.com/vistalumeworks</li>
      <li><span class="contact__key">F</span> : facebook.com/vistalumeworks</li>
      <li><span class="contact__key">M</span> : 0417 539 662</li>
    </ul>
    <div class="card__rule"></div>
    <div class="card__band">
      <p class="website">www.<strong>VISTALUMEWORKS</strong>.com.au</p>
    </div>
  </section>
</body>
</html>
```